New Business Card Design Project

I need a design for business cards, i am an electrical business called "Corvane Electrical and Communications" i need the cards to be double sided with the company logo on the back (attached) the front needs to say my company name, web site, email address, telephone number, and ABN number and electrical license number. I am open to different arrangements of the information but would like the background to be incorporating something electrical or something that looks smart. open to all additional ideas also.

The company colours are orange and grey see logo attached.

Business Name: Corvane Electrical and Communications
Website: corvaneelectricalandcomms.example.com.au
Email: brent@corvaneelectricalandcomms.example.com.au
Telephone(mobile): 0481209736
ABN: 71208349162
Lic No: 418273D

Target Market(s)

Business entities, Project Managers, Accounts, Clients

Industry/Entity Type

Electrician

Contact Information for Business Card

I need a design for business cards, i am an electrical business called "Corvane Electrical and Communications" i need the cards to be double sided with the company logo on the back (attached) the front needs to say my company name

Font styles to use
Serif
Sans Serif

Colors
f37122
5c5c5c

Requirements
Must have
• Must have the Logo on the back open to different ways of it being on the back but had in mind to keep it central but again open to other options
Nice to have
• A real modern cool background that is eye catching yet contemporary
Should not have
• No backgrounds of a light bulb or plug or anything like that

```html
<!DOCTYPE html>
<html lang="en">
<head>
<meta charset="utf-8">
<title>Corvane Electrical and Communications – Business Card</title>
<link href="https://fonts.googleapis.com/css2?family=Source+Sans+3:wght@400;600;700&display=swap" rel="stylesheet">
<style>
  :root {
    --stage: #000000;
    --card-light: #f3f3f3;
    --brand-orange: #f9ab1a;
    --ink: #111111;
    --white: #ffffff;
  }
  * { margin: 0; padding: 0; box-sizing: border-box; }
  html, body {
    width: 1200px; height: 900px; overflow: hidden;
    background: var(--stage);
    font-family: "Source Sans 3", Arial, sans-serif;
  }
  .canvas { position: relative; width: 1200px; height: 900px; }

  .card { position: absolute; top: 200px; width: 310px; height: 502px; }
  .card--front {
    left: 265px;
    background: var(--card-light);
    border-radius: 62px 0 62px 0;
  }
  .card--back {
    left: 641px; width: 309px;
    background: var(--brand-orange);
    border-radius: 0 62px 0 62px;
  }

  .wordmark { position: absolute; color: var(--ink); font-weight: 600; line-height: 1; }
  .wordmark__name { display: block; font-size: 44px; letter-spacing: 4px; }
  .wordmark__tag { display: block; font-size: 11.5px; letter-spacing: 0.9px; margin-top: 8px; }

  .card--front .wordmark { left: 53px; top: 94px; }
  .card--back .wordmark { left: 21px; top: 370px; color: var(--white); }
  .card--back .wordmark__name { font-size: 54px; letter-spacing: 7px; }
  .card--back .wordmark__tag { font-size: 13.5px; letter-spacing: 1.1px; margin-top: 10px; }

  .holder { position: absolute; left: 23px; top: 299px; }
  .holder__name { color: var(--brand-orange); font-size: 19px; font-weight: 600; line-height: 1.1; }
  .holder__role { color: var(--ink); font-size: 14px; line-height: 1.3; }

  .registration { position: absolute; left: 23px; top: 352px; color: var(--ink); font-size: 14px; line-height: 21px; }
  .registration b { font-weight: 700; font-size: 15px; }
  .registration span { font-weight: 600; }

  .contact { position: absolute; left: 23px; top: 410px; list-style: none; color: var(--ink); }
  .contact li { display: flex; align-items: center; height: 21px; font-size: 14px; }
  .contact li.contact--small { font-size: 11.2px; }
  .contact svg { width: 10px; height: 10px; margin-right: 8px; flex: none; fill: var(--brand-orange); }
</style>
</head>
<body>
<main class="canvas">

  <section class="card card--front" aria-label="Card front">
    <div class="wordmark">
      <span class="wordmark__name">CORVANE</span>
      <span class="wordmark__tag">ELECTRICAL &amp; COMMUNICATIONS</span>
    </div>

    <div class="holder">
      <p class="holder__name">Dale Warren</p>
      <p class="holder__role">Director</p>
    </div>

    <p class="registration">
      <b>ABN:</b> <span>71208349162</span><br>
      <b>Lic No:</b> <span>418273D</span>
    </p>

    <ul class="contact">
      <li>
        <svg viewBox="0 0 10 10" aria-hidden="true"><path d="M2 0.5 3.6 2.6 2.7 3.7C3.3 5 4.9 6.6 6.3 7.3L7.4 6.4 9.5 8 8.4 9.5C4.6 9.2 0.8 5.4 0.5 1.6Z"/></svg>
        0481209736
      </li>
      <li class="contact--small">
        <svg viewBox="0 0 10 10" aria-hidden="true"><path d="M0.5 2h9v6h-9z M0.5 2 5 5.6 9.5 2" stroke="#f3f3f3" stroke-width="0.8"/></svg>
        brent@corvaneelectricalandcomms.example.com.au
      </li>
      <li class="contact--small">
        <svg viewBox="0 0 10 10" aria-hidden="true"><circle cx="5" cy="5" r="4.6"/><path d="M2.5 3.5h2.5v2h-1.5zM5.8 6h2l-1 2z" fill="#f3f3f3"/></svg>
        corvaneelectricalandcomms.example.com.au
      </li>
    </ul>
  </section>

  <section class="card card--back" aria-label="Card back">
    <div class="wordmark">
      <span class="wordmark__name">CORVANE</span>
      <span class="wordmark__tag">ELECTRICAL &amp; COMMUNICATIONS</span>
    </div>
  </section>

</main>
</body>
</html>
```